Velmor Spire Nine Flash website

we need a website to cater to 2 aspect of the business. We have Velmor Spire Residence and Velmor Spire Office. For the office, we will get their inquire and arrange a face to face meetup to show them the office area for rent. For the residence side, it will need to be like staylane or roomvio.com. we want to allow them to book online for the date they need. We have a total of 10 different room configurations starting at $70 per night and up depending on the size of the room. example of the design is https://brisquelodge.com/

Target Market(s)

the website should have detail information on the layout, designs, and luxury of the building.

Industry/Entity Type

office and service appartment rental/lease

Coding

Coded - Design and coding required

Number of Pages Required

5+ page

Requirements
Must have
• a luxury perspective
Nice to have
• example https://brisquelodge.com/

```html
<!DOCTYPE html>
<html lang="en">
<head>
<meta charset="utf-8">
<title>Velmor Spire Nine</title>
<link rel="stylesheet" href="https://fonts.googleapis.com/css2?family=Cinzel:wght@400;500&family=Orbitron:wght@500;600&family=Poppins:wght@400;500;600;700&display=swap">
<style>
:root{
  --gold:#d39a2c;
  --gold-dark:#b9831f;
  --ink:#232323;
  --charcoal:#2c2c2c;
  --text:#4a4a4a;
  --muted:#777;
  --line:#d9d9d9;
  --paper:#ffffff;
  --board:#ffffff;
}
*{box-sizing:border-box;margin:0;padding:0}
html,body{width:1200px;height:4199px;overflow:hidden}
body{background:var(--board);font-family:"Poppins",sans-serif;color:var(--text);position:relative}
.panel{position:absolute;left:113px;width:960px;background:var(--paper);box-shadow:0 18px 45px rgba(0,0,0,.28);overflow:hidden}
.abs{position:absolute}
.display{font-family:"Orbitron",sans-serif;color:var(--ink);text-transform:uppercase;letter-spacing:1px}

/* splash */
.splash{top:163px;height:686px}
.splash-photo{position:absolute;inset:0;background:linear-gradient(180deg,#f4f4f4 0%,#ececec 45%,#e3e3e3 70%,#efefef 100%)}
.splash-mark{left:0;width:960px;top:210px;text-align:center}
.splash-mark .square{display:inline-block;width:86px;height:86px;border:3px solid var(--gold)}
.splash-title{left:0;width:960px;top:360px;text-align:center;font-family:"Cinzel",serif;font-size:56px;color:var(--gold);letter-spacing:1px}
.btn{display:flex;align-items:center;justify-content:center;gap:10px;font-weight:600}
.btn svg{width:9px;height:9px}
.splash-btn{top:455px;height:56px;font-size:19px}
.splash-btn.res{left:227px;width:264px;background:var(--gold);color:var(--ink)}
.splash-btn.off{left:508px;width:224px;background:var(--charcoal);color:var(--gold)}

/* home */
.home{top:979px;height:3008px}
.topstrip{top:0;left:0;width:960px;height:31px}
.topstrip span{position:absolute;top:8px;font-size:11px;color:var(--ink);display:flex;align-items:center;gap:6px}
.brand{left:42px;top:8px;display:flex;align-items:center;gap:10px;font-family:"Cinzel",serif;font-size:16px;color:var(--gold)}
.brand i{display:block;width:40px;height:52px;border:2px solid var(--gold)}
.navband{left:234px;top:31px;width:726px;height:45px;background:var(--gold);clip-path:polygon(28px 0,100% 0,100% 100%,0 100%)}
.nav a{position:absolute;top:45px;font-size:12px;font-weight:600;color:#fff;text-decoration:none}
.nav a.active{color:var(--ink)}
.nav-contact{left:788px;top:35px;width:116px;height:36px;background:var(--ink);color:#fff;font-size:12px}

.hero{top:76px;left:0;width:960px;height:466px}
.hero-photo{position:absolute;inset:0;background:linear-gradient(180deg,#dfe3e6 0%,#b9bec2 35%,#6f7377 70%,#4d5054 100%)}
.hero-shade{position:absolute;inset:0;background:linear-gradient(180deg,rgba(255,255,255,.15),rgba(0,0,0,.25))}
.hero-title{top:55px;left:0;width:923px;text-align:center;font-size:52px;font-weight:600;letter-spacing:3px}
.hero-sub{top:129px;left:0;width:923px;text-align:center;font-size:15px;font-weight:500;color:var(--ink);line-height:21px}
.hero-btn{top:198px;left:421px;width:118px;height:33px;background:var(--gold);color:var(--ink);font-size:12px}
.slider{top:420px;left:380px;display:flex;align-items:center;gap:6px;font-size:12px;font-weight:600;color:#fff}
.slider .on{color:var(--gold)}
.slider .bar{width:120px;height:2px;background:rgba(255,255,255,.5);position:relative}
.slider .bar::before{content:"";position:absolute;left:0;top:-1px;width:28px;height:3px;background:var(--gold)}
.sidebar{top:76px;left:923px;width:37px;height:466px;background:var(--ink)}
.sidebar .dot{position:absolute;left:9px;width:20px;height:20px;border:1.5px solid var(--gold);border-radius:50%}
.sidebar .sq{position:absolute;left:13px;width:11px;height:11px;border:1.5px solid #fff}
.sidebar .scroll{position:absolute;left:7px;top:215px;writing-mode:vertical-rl;font-size:10px;font-weight:600;color:#fff;letter-spacing:1px}

/* about */
.about-photo{left:84px;top:659px;width:335px;height:295px;background:linear-gradient(135deg,#e9e7e2 0%,#c9ccce 50%,#8e9296 100%)}
.about-photo-small{left:332px;top:817px;width:153px;height:126px;background:linear-gradient(135deg,#a9b7a3 0%,#6d7a70 60%,#4a524d 100%);border:6px solid #fff;box-sizing:content-box}
.section-head{font-size:28px;font-weight:600}
.section-head::after{content:"";display:block;width:68px;height:3px;background:var(--gold);margin-top:6px}
.about-head{left:519px;top:610px}
.about-copy{left:519px;top:663px;width:378px;font-size:11.5px;line-height:19.5px;color:var(--text);text-align:justify}
.about-copy p+p{margin-top:12px}
.about-btn{left:519px;top:898px;width:115px;height:37px;background:var(--gold);color:#fff;font-size:11.5px}
.about-or{left:649px;top:908px;font-size:11px;font-style:italic}
.about-call{left:688px;top:896px}
.about-call small{display:block;font-size:10.5px;font-style:italic;color:var(--muted)}
.about-call b{font-size:15px;font-weight:500;color:var(--ink)}

/* offices */
.offices{left:0;top:1022px;width:960px;height:1284px;background:var(--gold)}
.offices-head{left:0;width:960px;top:62px;text-align:center;font-size:30px}
.offices-head::after{margin:6px auto 0 66px;display:none}
.offices-head span{position:relative;display:inline-block}
.offices-head span::before{content:"";position:absolute;left:74px;bottom:-8px;width:150px;height:3px;background:var(--ink)}
.card{position:absolute;width:377px;height:478px;background:#fff}
.card-photo{position:absolute;left:0;top:0;width:377px;height:295px}
.card-photo::after{content:"";position:absolute;left:14px;top:12px;right:14px;bottom:12px;border:1px solid rgba(255,255,255,.75)}
.card h3{position:absolute;left:14px;top:318px;font-size:21px;font-weight:600}
.card p{position:absolute;left:15px;top:355px;width:340px;font-size:11.5px;line-height:20px;color:var(--text)}
.card .price{position:absolute;left:14px;top:412px;font-family:"Orbitron",sans-serif;font-size:25px;font-weight:600;color:var(--ink)}
.card .price small{font-size:18px}
.view-btn{left:422px;top:1176px;width:114px;height:35px;background:var(--charcoal);color:#fff;font-size:12px}

/* queries */
.q-bar{left:554px;top:2376px;width:406px;height:66px;background:#161616}
.q-head{left:127px;top:2426px}
.q-copy{left:127px;top:2482px;width:302px;font-size:12px;line-height:20px}
.q-contact{left:127px;display:flex;align-items:center;gap:14px}
.q-contact .ic{width:30px;height:30px;border-radius:50%;background:var(--gold);display:flex;align-items:center;justify-content:center}
.q-contact small{display:block;font-size:9.5px;color:var(--muted)}
.q-contact b{font-size:11.5px;font-weight:500;color:var(--ink)}
.q-social{top:2702px;left:127px;display:flex;gap:14px}
.q-social i{display:block;width:28px;height:28px;border:1.5px solid var(--gold);border-radius:50%}
.form{left:480px;top:2408px;width:361px;height:342px;background:#fff;box-shadow:0 10px 30px rgba(0,0,0,.18)}
.field{position:absolute;left:16px;width:329px;height:34px;border:1px solid #bdbdbd;font-size:10.5px;color:var(--ink);padding:9px 13px}
.submit{left:16px;top:284px;width:116px;height:34px;background:var(--gold);color:#fff;font-size:12px;justify-content:space-between;padding:0 18px}
.cta{left:127px;top:2738px;width:783px;height:123px;background:var(--gold);display:flex;align-items:center;padding-left:24px;gap:22px}
.cta span{font-family:"Orbitron",sans-serif;font-size:20px;font-weight:500;color:#fff;letter-spacing:1px}
.cta strong{font-family:"Orbitron",sans-serif;font-size:33px;font-weight:600;color:#fff;letter-spacing:2px}
.foot-nav{left:0;width:960px;top:2900px;display:flex;justify-content:center;gap:28px;font-size:11.5px;font-weight:600;color:var(--ink)}
.foot-line{left:89px;top:2945px;width:782px;height:1px;background:var(--line)}
.copyright{left:0;width:960px;top:2968px;text-align:center;font-size:11px;color:var(--text)}
</style>
</head>
<body>

<!-- Landing split screen -->
<section class="panel splash">
  <div class="splash-photo" role="img" aria-label="Bright open-plan office interior, heavily faded"></div>
  <div class="abs splash-mark"><span class="square"></span></div>
  <h1 class="abs splash-title">Velmor Spire Nine</h1>
  <a class="abs btn splash-btn res">Velmor Spire Residence <svg viewBox="0 0 10 10"><path d="M3 1l4 4-4 4" fill="none" stroke="currentColor" stroke-width="1.8"/></svg></a>
  <a class="abs btn splash-btn off">Velmor Spire Office <svg viewBox="0 0 10 10"><path d="M3 1l4 4-4 4" fill="none" stroke="currentColor" stroke-width="1.8"/></svg></a>
</section>

<!-- Office home page -->
<section class="panel home">
  <div class="abs topstrip">
    <span style="left:580px"><svg width="11" height="11" viewBox="0 0 24 24"><path d="M6.6 10.8a15 15 0 006.6 6.6l2.2-2.2a1 1 0 011-.25 11.4 11.4 0 003.6.57 1 1 0 011 1V20a1 1 0 01-1 1A17 17 0 013 4a1 1 0 011-1h3.5a1 1 0 011 1c0 1.25.2 2.45.57 3.6a1 1 0 01-.25 1z" fill="#d39a2c"/></svg>+1 555 014 2290</span>
    <span style="left:722px"><svg width="12" height="10" viewBox="0 0 24 18"><rect x="1" y="1" width="22" height="16" fill="#d39a2c"/><path d="M1 1l11 9 11-9" fill="none" stroke="#fff" stroke-width="2"/></svg>info@velmorspirenine.com</span>
  </div>
  <div class="abs brand"><i></i>Velmor Spire Nine</div>
  <div class="abs navband"></div>
  <nav class="nav">
    <a class="active" style="left:398px">Home</a>
    <a style="left:460px">About Us</a>
    <a style="left:540px">Our Office</a>
    <a style="left:628px">Testimonials</a>
    <a style="left:733px">Blog</a>
  </nav>
  <a class="abs btn nav-contact">Contact Us <svg viewBox="0 0 10 10"><path d="M3 1l4 4-4 4" fill="none" stroke="#fff" stroke-width="1.8"/></svg></a>

  <div class="abs hero">
    <div class="hero-photo" role="img" aria-label="Open-plan office with rows of white desks and orange task chairs"></div>
    <div class="hero-shade"></div>
    <h2 class="abs display hero-title">Velmor Spire Nine</h2>
    <p class="abs hero-sub">Saers lksos sepiciatisunde omnisiste natuserror sit<br>voluptatem ascusan tium doloremque.</p>
    <a class="abs btn hero-btn">Get Started <svg viewBox="0 0 10 10"><path d="M3 1l4 4-4 4" fill="none" stroke="currentColor" stroke-width="1.8"/></svg></a>
    <div class="abs slider"><span class="on">01</span><span class="bar"></span><span>05</span></div>
  </div>
  <div class="abs sidebar">
    <i class="dot" style="top:125px"></i>
    <i class="sq" style="top:157px"></i>
    <i class="sq" style="top:175px"></i>
    <span class="scroll">SCROLL DOWN</span>
    <svg class="abs" style="left:12px;top:300px" width="12" height="40" viewBox="0 0 12 40"><path d="M6 0v37M1 32l5 6 5-6" fill="none" stroke="#fff" stroke-width="1.3"/></svg>
  </div>

  <div class="abs about-photo" role="img" aria-label="Office interior with red chairs and white workstations"></div>
  <div class="abs about-photo-small" role="img" aria-label="Green-planted office lounge behind glass"></div>
  <h2 class="abs display section-head about-head">About Us</h2>
  <div class="abs about-copy">
    <p>Saerspiciatis undeasepoiise omnis istsaee natus esaerror sit voluptatem accusan tium doloremque laudantium, totam rem aperiam, ease aquhjfge ipaefdsa quaaseesae ab illo inventore veritatis ease quasi architecto beatae vitae dicta sunt explicabo. Nemo enim ipsoghjkm voluptathjkem qsaeseuia volupta sde sessitasese aspernatur autodit aadfdaseseut fugitsdsed quia consequuntur magni dolores eos nesciunt.</p>
    <p>Dseste natus error saseit voluptatem accusan tium doloremque laudantium, totam rem aperiam, ease aque ipaefdsa quae ab illo inventore veritatis ease quasi architecto.</p>
  </div>
  <a class="abs btn about-btn">Learn More <svg viewBox="0 0 10 10"><path d="M3 1l4 4-4 4" fill="none" stroke="#fff" stroke-width="1.8"/></svg></a>
  <span class="abs about-or">Or</span>
  <div class="abs about-call"><small>Call Us Now</small><b>+1 555 014 2290</b></div>

  <div class="abs offices">
    <h2 class="abs display offices-head"><span>Our Offices</span></h2>
    <article class="card" style="left:89px;top:143px">
      <div class="card-photo" role="img" aria-label="Bright office floor with white desk rows" style="background:linear-gradient(180deg,#e6e8ea,#a7abae 70%,#7e8285)"></div>
      <h3 class="display">Kdodms Aselinm</h3>
      <p>Oaunde omnsaeis sissaesgfte natfdgfus esrror sseit voluptatem accusantium dolseoremque laudantium.</p>
      <div class="price">$ 2000.00/<small>Month</small></div>
    </article>
    <article class="card" style="left:493px;top:143px">
      <div class="card-photo" role="img" aria-label="Loft office with brick wall and wooden floor" style="background:linear-gradient(135deg,#d9dde0,#a26a4e 60%,#6d4a38)"></div>
      <h3 class="display">Kdodms Aselinm</h3>
      <p>Oaunde omnsaeis sissaesgfte natfdgfus esrror sseit voluptatem accusantium dolseoremque laudantium.</p>
      <div class="price">$ 2000.00/<small>Month</small></div>
    </article>
    <article class="card" style="left:89px;top:653px">
      <div class="card-photo" role="img" aria-label="Industrial office with pendant lamps and blue lounge chairs" style="background:linear-gradient(180deg,#8c7b66,#c9cbcc 45%,#5f6e80)"></div>
      <h3 class="display">Kdodms Aselinm</h3>
      <p>Oaunde omnsaeis sissaesgfte natfdgfus esrror sseit voluptatem accusantium dolseoremque laudantium.</p>
      <div class="price">$ 2000.00/<small>Month</small></div>
    </article>
    <article class="card" style="left:493px;top:653px">
      <div class="card-photo" role="img" aria-label="Large open office with grey desk partitions" style="background:linear-gradient(180deg,#eceeef,#b3b7ba 60%,#8b8f92)"></div>
      <h3 class="display">Kdodms Aselinm</h3>
      <p>Oaunde omnsaeis sissaesgfte natfdgfus esrror sseit voluptatem accusantium dolseoremque laudantium.</p>
      <div class="price">$ 2000.00/<small>Month</small></div>
    </article>
    <a class="abs btn view-btn">View More <svg viewBox="0 0 10 10"><path d="M3 1l4 4-4 4" fill="none" stroke="#fff" stroke-width="1.8"/></svg></a>
  </div>

  <div class="abs q-bar"></div>
  <h2 class="abs display section-head q-head">For Queries</h2>
  <p class="abs q-copy">Dseste natus error sit voluptatem accusan tium doloremque laudantium, totam rem aperiam, ease aque ipaefdsa quae ab illo inventore veritatis ease quasi architecto.</p>
  <div class="abs q-contact" style="top:2604px"><span class="ic"><svg width="14" height="14" viewBox="0 0 24 24"><path d="M6.6 10.8a15 15 0 006.6 6.6l2.2-2.2a1 1 0 011-.25 11.4 11.4 0 003.6.57 1 1 0 011 1V20a1 1 0 01-1 1A17 17 0 013 4a1 1 0 011-1h3.5a1 1 0 011 1c0 1.25.2 2.45.57 3.6a1 1 0 01-.25 1z" fill="#fff"/></svg></span><div><small>Call Us</small><b>+1 555 014 2290</b></div></div>
  <div class="abs q-contact" style="top:2651px"><span class="ic"><svg width="14" height="11" viewBox="0 0 24 18"><rect x="1" y="1" width="22" height="16" fill="#fff"/><path d="M1 1l11 9 11-9" fill="none" stroke="#d39a2c" stroke-width="2"/></svg></span><div><small>Email</small><b>info@velmorspirenine.com</b></div></div>
  <div class="abs q-social"><i></i><i></i></div>

  <form class="abs form">
    <div class="field" style="top:26px">Your Name</div>
    <div class="field" style="top:74px">Email</div>
    <div class="field" style="top:121px">Phone Number</div>
    <div class="field" style="top:171px;height:98px">Enter Your Message</div>
    <a class="abs btn submit">Submit <svg viewBox="0 0 10 10"><path d="M3 1l4 4-4 4" fill="none" stroke="#fff" stroke-width="1.8"/></svg></a>
  </form>

  <div class="abs cta"><span>FOR MORE INFORMATION CALL US:</span><strong>+1 555 014 2290</strong></div>

  <nav class="abs foot-nav"><span>HOME</span><span>ABOUT US</span><span>OUR OFFICE</span><span>TESTIMONIALS</span><span>BLOG</span><span>CONTACT US</span></nav>
  <div class="abs foot-line"></div>
  <p class="abs copyright">©2024. All rights reserved.</p>
</section>

</body>
</html>
```